Dental Practice Website design

Design a new website for Brambleford Dental Practice.
Design should be warm, neutral in colour, with some small amount of bright colour if needed but kept to a minimum. Website should look professional, high end. Home page should be easy to navigate and simple for patients to be able to book online.
Logo in files along with some examples of websites that we like. Please ask if any further info needed.
Menu should have:
About
New Patients
Treatments
Fees
Contact Us

Industry/Entity Type

Dentistry

Number of Pages Required

4 page

Font styles to use
Sans Serif

Colors

Designer to choose colors to be used in the design.

Requirements
Must have
• Ravelle ratings badge, book online button,
Nice to have
• neutral, relaxing colours
Should not have
• harsh, bright colours!

```html
<!DOCTYPE html>
<html lang="en">
<head>
<meta charset="utf-8">
<title>Brambleford Dental Practice</title>
<link rel="stylesheet" href="https://fonts.googleapis.com/css2?family=Outfit:wght@300;400;500&family=Fraunces:opsz,wght@9..144,300;9..144,400&display=swap">
<style>
:root{
  --accent:#b3a297;
  --ink:#1d1a18;
  --text:#2b2624;
  --muted:#6a625e;
  --cream:#fbf8f3;
  --mist:#eef3f5;
  --topbar:#f4f3f2;
  --footer:#b5a59b;
  --white:#ffffff;
  --blush:#fbeef2;
  --peach:#f1d3c8;
  --terracotta:#d9a491;
  --card-general:#f3e4d0;
  --card-cosmetic:#bfe3e8;
  --card-ortho:#e1d3de;
  --card-prevent:#e6ebd1;
  --serif:"Fraunces", Georgia, serif;
  --sans:"Outfit", Arial, sans-serif;
}
*{margin:0;padding:0;box-sizing:border-box}
html,body{width:1200px;height:3771px;overflow:hidden;background:var(--white)}
body{position:relative;font-family:var(--sans);color:var(--text);font-weight:300}
.abs{position:absolute}
.btn{position:absolute;background:var(--accent);color:var(--white);font-family:var(--sans);font-size:15px;font-weight:400;text-transform:uppercase;display:flex;align-items:center;justify-content:center;white-space:nowrap}
.heading{font-family:var(--serif);color:var(--ink);font-weight:400;white-space:nowrap;line-height:1.2}
.soft{color:var(--accent);font-weight:300}
.rule{position:absolute;height:2px;background:var(--accent)}
.photo{position:absolute}
.dots{position:absolute;background:rgba(60,50,45,.035);border-radius:4px}
.topbar{position:absolute;left:0;top:0;width:1200px;height:85px;background:var(--topbar)}
.brand{position:absolute;left:111px;top:25px;display:flex;align-items:center;gap:8px;font-size:14px;line-height:16px;color:#4a4440;font-weight:400;text-transform:uppercase}
.brand .mark{width:12px;height:12px;background:#4a4440}
.contact{position:absolute;top:0;height:85px;display:flex;align-items:center;gap:22px;font-size:11.5px;color:#5a5450;text-transform:uppercase;line-height:22px;white-space:nowrap}
.contact .ico{width:28px;height:28px;background:var(--accent);display:flex;align-items:center;justify-content:center}
.nav{position:absolute;top:104px;left:111px;display:flex;font-size:13px;text-transform:uppercase;color:#3a3532;font-weight:400;white-space:nowrap}
.nav a{color:inherit;text-decoration:none;margin-right:35px}
.nav a.current{color:var(--accent)}
.hero{position:absolute;left:0;top:139px;width:1200px;height:465px;background:linear-gradient(90deg,var(--blush) 0%,#f8e4e6 45%,var(--peach) 72%,var(--terracotta) 100%)}
.hero p{font-size:14.5px;line-height:36px;color:var(--text)}
.services{position:absolute;left:0;top:1266px;width:1200px;height:783px;background:var(--cream)}
.card{position:absolute;top:298px;width:236px;height:341px;text-align:center}
.card .icon{width:70px;height:70px;border-radius:50%;background:rgba(255,255,255,.85);margin:29px auto 0;display:flex;align-items:center;justify-content:center}
.card h3{font-family:var(--serif);font-weight:400;font-size:19px;color:var(--ink);margin-top:30px;white-space:nowrap}
.card p{font-size:14.5px;line-height:36px;color:var(--muted);margin:14px 24px 0}
.team{position:absolute;left:0;top:2651px;width:1200px;height:846px;background:var(--mist)}
.member{position:absolute;width:189px;text-align:center}
.member .portrait{width:189px;height:256px;background:linear-gradient(180deg,#e9ecef,#cfd5db)}
.member .name{font-family:var(--serif);font-size:15px;color:var(--ink);margin-top:28px;white-space:nowrap}
.footer-links{position:absolute;top:3664px;left:0;width:1200px;display:flex;justify-content:center;font-size:13px;color:var(--white);text-transform:uppercase;white-space:nowrap}
.footer-links span{padding:0 20px}
</style>
</head>
<body>

<header class="topbar">
  <div class="brand"><span class="mark"></span><span>Brambleford<br>Dental Practice</span></div>
  <div class="contact" style="left:305px">
    <span class="ico"><svg width="12" height="16" viewBox="0 0 12 16"><path d="M6 0a6 6 0 0 0-6 6c0 4.5 6 10 6 10s6-5.5 6-10a6 6 0 0 0-6-6zm0 8.5A2.5 2.5 0 1 1 6 3.5a2.5 2.5 0 0 1 0 5z" fill="#fff"/></svg></span>
    <span>12, Willow Lane<br>Brambleford BF1 4QT</span>
  </div>
  <div class="contact" style="left:570px">
    <span class="ico"><svg width="14" height="14" viewBox="0 0 24 24"><path d="M6.6 10.8a15 15 0 0 0 6.6 6.6l2.2-2.2c.3-.3.7-.4 1-.2 1.1.4 2.3.6 3.6.6.6 0 1 .4 1 1V20c0 .6-.4 1-1 1A17 17 0 0 1 3 4c0-.6.4-1 1-1h3.5c.6 0 1 .4 1 1 0 1.3.2 2.5.6 3.6.1.3 0 .7-.2 1z" fill="#fff"/></svg></span>
    <span>+44 1632 960 418</span>
  </div>
  <div class="contact" style="left:803px">
    <span class="ico"><svg width="14" height="11" viewBox="0 0 14 11"><rect x="0.5" y="0.5" width="13" height="10" fill="none" stroke="#fff"/><path d="M.5 .5 7 6l6.5-5.5" fill="none" stroke="#fff"/></svg></span>
    <span>hello@bramblefordental.co.uk</span>
  </div>
</header>

<nav class="nav">
  <a class="current">Home</a><a>About</a><a>New Patients</a><a>Treatments</a><a>Fees</a><a>Contact Us</a>
</nav>
<div class="btn" style="left:913px;top:98px;width:176px;height:30px;font-size:12px">Make an Appointment</div>

<section class="hero">
  <div class="photo" role="img" aria-label="Smiling woman holding a hand mirror, checking her teeth" style="left:620px;top:0;width:580px;height:465px;background:linear-gradient(90deg,rgba(248,228,230,0) 0%,rgba(230,190,175,.35) 60%,rgba(210,150,130,.45) 100%)"></div>
  <h1 class="heading abs" style="left:109px;top:66px;font-size:42px">Caring for Your Smile,</h1>
  <h2 class="heading abs soft" style="left:109px;top:130px;font-size:30px">Comforting Your Soul.</h2>
  <p class="abs" style="left:111px;top:193px;width:505px">Welcome to our friendly dental practice nestled in the heart of beautiful Brambleford, Hartshire. Our team of dedicated dentists, hygienists and support staff are here to provide you with exceptional dental care.</p>
  <div class="btn" style="left:111px;top:335px;width:130px;height:39px">Book Online</div>
  <svg class="abs" style="left:0;top:0" width="1200" height="465"><polygon points="0,400 0,465 135,465" fill="#fff"/><polygon points="1200,380 1200,465 1060,465" fill="#fff"/></svg>
</section>

<section>
  <div class="photo" role="img" aria-label="Dental team reviewing notes in the clinic" style="left:111px;top:688px;width:262px;height:212px;background:linear-gradient(135deg,#eef0f1,#c9d1d6)"></div>
  <div class="photo" role="img" aria-label="Dentist examining a patient in the chair" style="left:111px;top:926px;width:262px;height:256px;background:linear-gradient(135deg,#d6dde2,#9fb4bf)"></div>
  <div class="photo" role="img" aria-label="Young girl receiving a dental check-up" style="left:827px;top:688px;width:262px;height:304px;background:linear-gradient(135deg,#bfe0ec,#6fa9c6)"></div>
  <div class="photo" role="img" aria-label="Patient having a curing light applied to her teeth" style="left:827px;top:1017px;width:262px;height:166px;background:linear-gradient(135deg,#d8e4ec,#c7a892)"></div>
  <h2 class="heading abs" style="left:380px;width:440px;top:680px;text-align:center;font-size:30px">Welcome to</h2>
  <h2 class="heading abs soft" style="left:380px;width:440px;top:733px;text-align:center;font-size:28px">Brambleford Dental Practice</h2>
  <div class="rule" style="left:550px;top:785px;width:100px"></div>
  <p class="abs" style="left:405px;top:815px;width:390px;text-align:center;font-size:14.5px;line-height:33.5px;color:var(--text)">At our practice, we believe that a visit to the dentist should be a comfortable and positive experience. We strive to create a warm and welcoming atmosphere where our patients can feel at ease and confident in the care they receive. Our state-of-the-art facilities and equipment mean that you can trust us to deliver the latest techniques and treatments to ensure your oral health is at its best we are passionate about improving dental health</p>
  <div class="btn" style="left:535px;top:1146px;width:130px;height:38px">Learn More</div>
</section>

<section class="services">
  <div class="dots" role="img" aria-label="Dotted decoration" style="left:42px;top:60px;width:113px;height:52px"></div>
  <div class="dots" role="img" aria-label="Dotted decoration" style="left:1035px;top:682px;width:115px;height:52px"></div>
  <h2 class="heading abs" style="left:0;width:1200px;top:62px;text-align:center;font-size:30px">Brambleford Dental Practice <span class="soft">Services</span></h2>
  <p class="abs" style="left:190px;width:820px;top:148px;text-align:center;font-size:14.5px;line-height:36px;color:var(--text)">At Brambleford Dental Practice, we offer a comprehensive range of dental services to meet the needs of our patients. Whether you need routine care, cosmetic enhancements, or more specialized treatment, our expert team is here to guide you every step of the way.</p>
  <div class="card" style="left:111px;background:var(--card-general)"><div class="icon"><svg width="34" height="34" viewBox="0 0 34 34" fill="none" stroke="#b3a297" stroke-width="1.4"><path d="M9 5c-4 0-6 4-5 9 1 4 2 6 3 12 .5 3 3 3 3.5 0l1.5-7c.5-2 3.5-2 4 0l1.5 7c.5 3 3 3 3.5 0 1-6 2-8 3-12 1-5-1-9-5-9-3 0-4 2-5 2s-2-2-5-2z"/></svg></div><h3>General Dentistry</h3><p>We provide a full range of general dentistry services to keep your smile healthy and bright.</p></div>
  <div class="card" style="left:358px;background:var(--card-cosmetic)"><div class="icon"><svg width="34" height="34" viewBox="0 0 34 34" fill="none" stroke="#b3a297" stroke-width="1.4"><path d="M5 20c4 6 20 6 24 0"/><path d="M9 20c2-5 14-5 16 0"/><path d="M20 14 28 6"/></svg></div><h3>Cosmetic Dentistry</h3><p>We provide a full range of general dentistry services to keep your smile healthy and bright.</p></div>
  <div class="card" style="left:606px;background:var(--card-ortho)"><div class="icon"><svg width="34" height="34" viewBox="0 0 34 34" fill="none" stroke="#b3a297" stroke-width="1.4"><path d="M9 6c-4 0-6 4-5 9 1 4 2 6 3 12 .5 3 3 3 3.5 0l1.5-7c.5-2 3.5-2 4 0l1.5 7c.5 3 3 3 3.5 0 1-6 2-8 3-12 1-5-1-9-5-9-3 0-4 2-5 2s-2-2-5-2z"/><path d="M6 13h22"/><rect x="11" y="11" width="4" height="4"/><rect x="19" y="11" width="4" height="4"/></svg></div><h3>Orthodontics</h3><p>We provide a full range of general dentistry services to keep your smile healthy and bright.</p></div>
  <div class="card" style="left:853px;background:var(--card-prevent)"><div class="icon"><svg width="34" height="34" viewBox="0 0 34 34" fill="none" stroke="#b3a297" stroke-width="1.4"><path d="M17 20s-7-4-7-9a3.5 3.5 0 0 1 7-1 3.5 3.5 0 0 1 7 1c0 5-7 9-7 9z"/><path d="M4 14v8l6 6M30 14v8l-6 6"/></svg></div><h3>Preventative Care</h3><p>We provide a full range of general dentistry services to keep your smile healthy and bright.</p></div>
  <div class="btn" style="left:504px;top:680px;width:192px;height:39px">View More Services</div>
</section>

<section>
  <div class="dots" role="img" aria-label="Dotted decoration" style="left:84px;top:2110px;width:106px;height:110px"></div>
  <div class="abs" style="left:103px;top:2140px;width:456px;height:428px;border:2px solid #cfc6c0;border-radius:12px"></div>
  <div class="photo" role="img" aria-label="Two dentists treating a reclining patient" style="left:111px;top:2136px;width:447px;height:424px;border-radius:10px;background:linear-gradient(135deg,#e7eef3,#9cc0de 60%,#6f9fcf)"></div>
  <h2 class="heading abs" style="left:624px;top:2148px;font-size:30px">Join Our <span class="soft">Practice</span></h2>
  <div class="rule" style="left:624px;top:2202px;width:102px"></div>
  <p class="abs" style="left:624px;top:2236px;width:470px;font-size:14.5px;line-height:33.5px;color:var(--text)">If you're looking for an exceptional dental practice, we're here to help! Our team is made up of highly skilled professionals who are dedicated to ensuring that all our patients receive top-notch care in a welcoming and comfortable environment.</p>
  <p class="abs" style="left:624px;top:2382px;width:470px;font-size:14.5px;line-height:33.5px;color:var(--text)">Whether you need a routine examination or a more specialised treatment, we have all the resources to provide you with the best dental care possible.</p>
  <div class="btn" style="left:624px;top:2512px;width:112px;height:37px">Join Now</div>
</section>

<section class="team">
  <div class="dots" role="img" aria-label="Dotted decoration" style="left:1037px;top:47px;width:115px;height:55px"></div>
  <div class="dots" role="img" aria-label="Dotted decoration" style="left:38px;top:749px;width:114px;height:55px"></div>
  <h2 class="heading abs" style="left:0;width:1200px;top:60px;text-align:center;font-size:30px">Our <span class="soft">Team</span></h2>
  <div class="rule" style="left:552px;top:114px;width:96px"></div>
  <p class="abs" style="left:170px;width:860px;top:144px;text-align:center;font-size:14.5px;line-height:33.5px;color:var(--text)">We are delighted to introduce you to our experienced and compassionate dental team. Our team comprises highly skilled dental professionals who are dedicated to providing you with high-quality dental care services.</p>
  <div class="btn" style="left:521px;top:239px;width:158px;height:38px">Meet Our Team</div>
  <div class="member" style="left:111px;top:346px"><div class="portrait" role="img" aria-label="Portrait of a dentist in a white coat"></div><div class="name">Dr. Helena Marsh</div></div>
  <div class="member" style="left:308px;top:412px"><div class="portrait" role="img" aria-label="Portrait of a dental hygienist in a white coat"></div><div class="name">Sophie Linwood</div></div>
  <div class="member" style="left:506px;top:353px"><div class="portrait" role="img" aria-label="Portrait of a dentist with a stethoscope"></div><div class="name">Dr. Owen Fairley</div></div>
  <div class="member" style="left:703px;top:483px"><div class="portrait" role="img" aria-label="Portrait of a dental nurse holding a tablet"></div><div class="name">Clara Benning</div></div>
  <div class="member" style="left:900px;top:379px"><div class="portrait" role="img" aria-label="Portrait of a dentist with arms crossed"></div><div class="name">Theo Ashby</div></div>
</section>

<footer>
  <svg class="abs" style="left:0;top:3497px" width="1200" height="274"><polygon points="130,0 1070,0 1200,58 1200,274 0,274 0,58" fill="#b5a59b"/></svg>
  <div class="abs" style="left:0;width:1200px;top:3568px;display:flex;justify-content:center;align-items:center;gap:10px;color:var(--white);font-size:20px;text-transform:uppercase;line-height:22px;text-align:center;font-weight:400">
    <span style="width:14px;height:14px;background:var(--white)"></span><span>Brambleford<br>Dental Practice</span>
  </div>
  <div class="footer-links"><span>Home</span>|<span>About</span>|<span>New Patients</span>|<span>Treatments</span>|<span>Fees</span>|<span>Contact Us</span></div>
  <div class="abs" style="left:0;width:1200px;top:3710px;text-align:center;font-size:13px;color:var(--white);text-transform:uppercase;word-spacing:2px">©2025 Copyrights &nbsp;&nbsp;&nbsp;|&nbsp;&nbsp;&nbsp; All Rights Reserved</div>
  <div class="abs" style="left:14px;top:3708px;width:180px;height:54px;background:var(--white);box-shadow:0 1px 5px rgba(0,0,0,.3);border-top:3px solid #8ab4a0;display:flex;align-items:center;gap:10px;padding-left:10px">
    <span style="width:32px;height:32px;border-radius:50%;background:#d9d2cc"></span>
    <span style="font-size:12px;line-height:17px;color:#444;white-space:nowrap">Ravelle Rated<br><span style="color:#b58a3c">5.0 ★★★★★</span></span>
  </div>
</footer>

</body>
</html>
```